Business Card Design Project - del varosi group

dear Sirs

we need business card design for our group ( DEL Varosi Group ) , i have got the Logo design of our group from pixel harbor in previous , so all need details relating to our group i think available with you, as well as the the chosen logo design

we hope to provide us with business card logo that to be appropaite and satisfactory to us .

thanks

note : logo design of our group is attached .
Updates

Reason: please extend the deadline of my project for additional 15 days because i didn't received appropriate design for our gruop yet . kindly beaware that i have received 77 design till now , supossed to send me 200-250 design at least . thanks

Target Market(s)

contents

name : Kerem EL Nadiri

position : Operation Manager

Industry/Entity Type

Business

Requirements
Must have

• person name

group logo
Nice to have
• logo color matching with back background

```html
<!DOCTYPE html>
<html lang="en">
<head>
<meta charset="utf-8">
<title>DEL Varosi Group – Business Card</title>
<link rel="stylesheet" href="https://fonts.googleapis.com/css2?family=Arimo:wght@400&family=Open+Sans:wght@400;600;700&display=swap">
<style>
  :root {
    --stage: #e4e6ea;
    --brand-blue: #1a4f94;
    --brand-deep: #0f3f7e;
    --brand-light: #5b95cf;
    --brand-gold: #c49a3c;
    --ink: #1d1d1d;
    --card-white: #ffffff;
  }
  * { box-sizing: border-box; margin: 0; padding: 0; }
  html, body { width: 1200px; height: 900px; overflow: hidden; }
  body {
    background: var(--stage);
    font-family: "Open Sans", Arial, sans-serif;
    display: flex;
    flex-direction: column;
    align-items: center;
    justify-content: center;
    gap: 40px;
  }
  .card {
    width: 630px;
    height: 360px;
    border-radius: 26px;
    position: relative;
    overflow: hidden;
    box-shadow: 0 6px 18px rgba(0,0,0,.18);
  }

  /* Back side */
  .card-back {
    background: radial-gradient(ellipse at 45% 40%, var(--brand-light) 0%, #2f6cb0 40%, var(--brand-deep) 85%);
    display: flex;
    align-items: center;
    justify-content: center;
  }
  .back-wordmark {
    display: flex;
    align-items: center;
    gap: 14px;
    color: var(--card-white);
    font-weight: 700;
    font-size: 40px;
    letter-spacing: 1px;
  }
  .back-wordmark .mark-square {
    width: 30px; height: 30px;
    background: var(--brand-gold);
  }

  /* Front side */
  .card-front { background: var(--card-white); }
  .edge-tab {
    position: absolute;
    left: 0; top: 24px;
    width: 8px; height: 52px;
    background: var(--brand-blue);
    border-radius: 0 6px 6px 0;
  }
  .front-wordmark {
    position: absolute;
    left: 30px; top: 34px;
    display: flex;
    align-items: center;
    gap: 10px;
    color: var(--brand-blue);
    font-weight: 600;
    font-size: 30px;
    letter-spacing: .5px;
  }
  .front-wordmark .mark-square {
    width: 20px; height: 20px;
    background: var(--brand-blue);
  }
  .person {
    position: absolute;
    left: 50px; top: 140px;
  }
  .person-name {
    font-family: "Arimo", Arial, sans-serif;
    color: var(--brand-blue);
    font-size: 24px;
    font-weight: 400;
  }
  .person-role {
    font-size: 16px;
    color: var(--ink);
    margin-top: 2px;
  }
  .contact {
    position: absolute;
    left: 350px; top: 170px;
  }
  .address {
    color: var(--brand-blue);
    font-weight: 700;
    font-size: 15px;
    line-height: 18px;
    margin-bottom: 14px;
  }
  .contact-line {
    display: flex;
    align-items: center;
    gap: 14px;
    font-size: 16px;
    color: var(--ink);
    line-height: 22px;
  }
  .contact-line svg { width: 18px; height: 16px; flex: none; }
  .bottom-band {
    position: absolute;
    left: 0; right: 0; bottom: 0;
    height: 7px;
    background: var(--brand-blue);
  }
  .web-tab {
    position: absolute;
    left: 335px; bottom: 0;
    width: 230px; height: 36px;
    background: var(--brand-blue);
    border-radius: 10px 10px 0 0;
    color: var(--card-white);
    font-size: 16px;
    display: flex;
    align-items: center;
    justify-content: center;
    letter-spacing: .3px;
  }
</style>
</head>
<body>

  <section class="card card-back" aria-label="Card back">
    <div class="back-wordmark"><span class="mark-square"></span>DEL VAROSI GROUP</div>
  </section>

  <section class="card card-front" aria-label="Card front">
    <span class="edge-tab"></span>
    <div class="front-wordmark"><span class="mark-square"></span>DEL VAROSI GROUP</div>

    <div class="person">
      <p class="person-name">Kerem EL Nadiri</p>
      <p class="person-role">Operation Manager</p>
    </div>

    <div class="contact">
      <p class="address">P.O. Box: 40718<br>Sharjah United Arab Emirates</p>
      <p class="contact-line">
        <svg viewBox="0 0 18 16" aria-hidden="true"><path fill="#1a4f94" d="M4 1l3 3-2 2c1 2 3 4 5 5l2-2 3 3-2 3C7 15 2 10 1 4z"/></svg>
        (+11) 555 010 4821
      </p>
      <p class="contact-line">
        <svg viewBox="0 0 18 16" aria-hidden="true"><rect x="2" y="5" width="14" height="8" rx="1.5" fill="#1a4f94"/><rect x="5" y="1" width="8" height="5" fill="none" stroke="#1a4f94" stroke-width="1.5"/><rect x="5" y="9" width="8" height="5" fill="#fff"/></svg>
        (+11) 555 010 4823
      </p>
      <p class="contact-line">
        <svg viewBox="0 0 18 16" aria-hidden="true"><rect x="1" y="3" width="16" height="11" fill="#1a4f94"/><path d="M1 3l8 6 8-6" fill="none" stroke="#fff" stroke-width="1.2"/></svg>
        info@delvarosi.com
      </p>
    </div>

    <div class="bottom-band"></div>
    <div class="web-tab">www.delvarosi.com</div>
  </section>

</body>
</html>
```